Icons/images for company values

We have five company values, we have a new logo and a new look. I would like drawn images for each value that are in keeping with our look and feel.

Target Market(s)

internal/staff

Industry/Entity Type

media compliance

Requirements
Must have
• colours aligned with logo.

```html
<!DOCTYPE html>
<html lang="en">
<head>
<meta charset="utf-8">
<title>Values 2023</title>
<link rel="stylesheet" href="https://fonts.googleapis.com/css2?family=Poppins:wght@400;500;600;700&display=swap">
<style>
:root{
  --page:#ececec;
  --card:#ffffff;
  --navy:#3b6689;
  --blue-1:#3a6b98;
  --blue-2:#5a9ec9;
  --teal:#78c4a6;
  --lime:#a9d27a;
  --yellow:#ead84f;
  --olive:#a4962a;
  --ink:#1d2a33;
  --ring:#c9d6de;
  --rule:#9fb6c8;
}
*{margin:0;padding:0;box-sizing:border-box}
html,body{width:707px;height:1200px;overflow:hidden;background:var(--page);font-family:"Poppins",sans-serif}
.values-board{position:absolute;left:0;top:327px;width:707px;height:546px;background:var(--card);box-shadow:0 4px 18px rgba(0,0,0,.12)}
.values-graphic{position:absolute;left:0;top:0}
.brand-name{position:absolute;left:30px;top:90px;font-family:"Poppins",sans-serif;font-weight:500;font-size:21px;letter-spacing:6px;color:var(--blue-2)}
.value{position:absolute}
.value-title{font-weight:700;font-size:14px;line-height:1.1;text-transform:uppercase;letter-spacing:.1px}
.value-text{font-weight:400;font-size:10.3px;line-height:1.2;color:var(--ink);margin-top:3px;white-space:nowrap}
.value--open{left:276px;top:49px}
.value--open .value-title{color:var(--blue-1)}
.value--together{left:363px;top:132px}
.value--together .value-title{color:var(--blue-2)}
.value--leaders{left:398px;top:233px}
.value--leaders .value-title{color:var(--teal)}
.value--leaders .value-text{margin-top:7px}
.value--done{left:363px;top:369px}
.value--done .value-title{color:var(--lime)}
.value--diverse{left:276px;top:448px}
.value--diverse .value-title{color:var(--olive);font-size:13.4px;letter-spacing:-.1px}
.divider{position:absolute;height:0;border-top:1px dotted var(--rule)}
.divider--1{left:329px;top:110px;width:315px}
.divider--2{left:358px;top:204px;width:286px}
.divider--3{left:358px;top:344px;width:286px}
.divider--4{left:324px;top:431px;width:320px}
</style>
</head>
<body>
<main class="values-board">
  <svg class="values-graphic" width="707" height="546" viewBox="0 0 707 546" aria-hidden="true">
    <defs>
      <linearGradient id="seg1" x1="0" y1="0" x2="1" y2="1"><stop offset="0" stop-color="#356590"/><stop offset="1" stop-color="#4a82b6"/></linearGradient>
      <linearGradient id="seg2" x1="0" y1="0" x2="1" y2="1"><stop offset="0" stop-color="#5aa0d0"/><stop offset="1" stop-color="#63aeb3"/></linearGradient>
      <linearGradient id="seg3" x1="0" y1="0" x2="0" y2="1"><stop offset="0" stop-color="#6fc0ad"/><stop offset="1" stop-color="#8ed49d"/></linearGradient>
      <linearGradient id="seg4" x1="0" y1="0" x2="0" y2="1"><stop offset="0" stop-color="#9fd88f"/><stop offset="1" stop-color="#cddc66"/></linearGradient>
      <linearGradient id="seg5" x1="0" y1="0" x2="0" y2="1"><stop offset="0" stop-color="#e3d555"/><stop offset="1" stop-color="#f0dc4e"/></linearGradient>
    </defs>

    <!-- connector line -->
    <g class="connector" fill="none" stroke="var(--navy)" stroke-width="2">
      <path d="M43 183 V412 H143"/>
      <circle cx="43" cy="179" r="4" fill="#fff"/>
      <circle cx="147" cy="412" r="4" fill="#fff"/>
    </g>

    <!-- fan segments -->
    <g class="fan">
      <path fill="url(#seg1)" d="M160 75 A192 192 0 0 1 265.6 109.3 L215.4 181.6 A104 104 0 0 0 158.2 163 Z"/>
      <path fill="url(#seg2)" d="M272.1 114.1 A192 192 0 0 1 337.3 203.9 L254.2 232.8 A104 104 0 0 0 218.9 184.2 Z"/>
      <path fill="url(#seg3)" d="M339.8 211.5 A192 192 0 0 1 339.8 322.5 L255.6 297.1 A104 104 0 0 0 255.6 236.9 Z"/>
      <path fill="url(#seg4)" d="M337.3 330.1 A192 192 0 0 1 272.1 419.9 L218.9 349.8 A104 104 0 0 0 254.2 301.2 Z"/>
      <path fill="url(#seg5)" d="M265.6 424.7 A192 192 0 0 1 160 459 L158.2 371 A104 104 0 0 0 215.4 352.4 Z"/>
    </g>

    <!-- segment icons -->
    <g class="icons" fill="none" stroke="#fff" stroke-width="2" stroke-linecap="round" stroke-linejoin="round">
      <path d="M202 152 C190 143 190 134 196 133 C199 132 201 134 202 136 C203 134 205 132 208 133 C214 134 214 143 202 152 Z" fill="#fff"/>
      <path d="M191 147 L196 156 M213 147 L208 156"/>
      <circle cx="280" cy="194" r="7"/>
      <path d="M270 192 A11 11 0 0 1 288 184 M290 196 A11 11 0 0 1 272 204"/>
      <path d="M288 184 l1 -4 M272 204 l-1 4"/>
      <circle cx="303" cy="263" r="8"/>
      <path d="M299 263 l3 3 l5 -6"/>
      <path d="M299 274 h8 M300 278 h6 M291 263 h-4 M315 263 h4 M303 251 v-4"/>
      <circle cx="285" cy="322" r="6"/>
      <circle cx="285" cy="322" r="10" stroke-dasharray="3 2.5"/>
      <path d="M277 338 h16 v6 h-16 z" fill="#fff"/>
      <circle cx="207" cy="410" r="4" fill="#fff"/>
      <path d="M199 428 l8 -12 l8 12 M194 424 l5 4 M220 424 l-5 4"/>
    </g>

    <!-- centre medallion -->
    <circle cx="156" cy="267" r="104" fill="#fff" stroke="var(--ring)" stroke-width="1"/>
    <circle cx="156" cy="267" r="88" fill="var(--navy)"/>
    <text x="156" y="252" text-anchor="middle" fill="#fff" font-family="Poppins, sans-serif" font-weight="500" font-size="25">VALUES</text>
    <text x="156" y="290" text-anchor="middle" fill="#fff" font-family="Poppins, sans-serif" font-weight="500" font-size="40">2023</text>

    <!-- number badges -->
    <g class="badges" fill="#fff" stroke="var(--blue-1)" stroke-width="2.4">
      <circle cx="223" cy="79" r="34"/>
      <circle cx="316" cy="162" r="34"/>
      <circle cx="347" cy="275" r="34"/>
      <circle cx="311" cy="389" r="34"/>
      <circle cx="208" cy="457" r="34"/>
    </g>
    <g class="badge-numbers" fill="var(--blue-1)" font-family="Poppins, sans-serif" font-weight="600" font-size="25" text-anchor="middle">
      <text x="223" y="88">01</text>
      <text x="316" y="171">02</text>
      <text x="347" y="284">03</text>
      <text x="311" y="398">04</text>
      <text x="208" y="466">05</text>
    </g>
  </svg>

  <div class="brand-name">NORVA</div>

  <section class="value value--open">
    <h2 class="value-title">We're open and honest</h2>
    <p class="value-text">Sharing information helps us achieve the best outcomes for our teams<br>and business. We value open, honest, and clear communication.</p>
  </section>
  <div class="divider divider--1"></div>

  <section class="value value--together">
    <h2 class="value-title">We get&nbsp; there faster together</h2>
    <p class="value-text">Collaboration is at the heart of what we do, no<br>matter our team</p>
  </section>
  <div class="divider divider--2"></div>

  <section class="value value--leaders">
    <h2 class="value-title">We are leaders in copyright<br>and intellectual property</h2>
    <p class="value-text">Leading the conversation in audio-visual<br>copyright compliance and advocating for<br>the protection of intellectual property globally.</p>
  </section>
  <div class="divider divider--3"></div>

  <section class="value value--done">
    <h2 class="value-title">We get things done</h2>
    <p class="value-text">We grow through capability, focus and hard work. We<br>believe small steps compound to bigresults.</p>
  </section>
  <div class="divider divider--4"></div>

  <section class="value value--diverse">
    <h2 class="value-title">Diverse perspectives build better outcomes</h2>
    <p class="value-text">We value diversity, inclusion, respect and trust within our teams. We are<br>building a truly global organisation.</p>
  </section>
</main>
</body>
</html>
```